Compnay PowerPoint Tempalte Design

I am needing a good base design and slide designs for interior and exterior company presentations. The template will need to be on the company brand with proper coloring and fonts. Able to be creative with layout options with a good example attached.
website for reference: www.crewvlt.com/

Target Market(s)

Professionals

Font styles to use
Other font styles liked:
• Helvetica

Requirements
Must have
• On Brand Colors, Clean, simple design

```html
<!DOCTYPE html>
<html lang="en">
<head>
<meta charset="utf-8">
<title>CREWVLT Presentation Template</title>
<link href="https://fonts.googleapis.com/css2?family=Roboto:wght@300;400;700&display=swap" rel="stylesheet">
<style>
:root{
  --navy:#0f4f9c;
  --blue:#1663b0;
  --teal:#1b8c9c;
  --deep-teal:#1f6e6a;
  --gold:#b6a35a;
  --red:#b24a55;
  --green:#4b8a7a;
  --ink:#4a4f55;
  --muted:#8a9096;
  --paper:#ffffff;
  --page:#ffffff;
}
*{margin:0;padding:0;box-sizing:border-box}
html,body{width:1200px;height:1200px;overflow:hidden;background:var(--page)}
body{font-family:"Roboto",Helvetica,Arial,sans-serif;color:var(--ink);position:relative}
.defs{position:absolute;width:0;height:0}
.slide{position:absolute;width:312px;height:176px;background:var(--paper);overflow:hidden;box-shadow:0 3px 10px rgba(0,0,0,.28)}
.c1{left:61px}.c2{left:447px}.c3{left:834px}
.r1{top:29px}.r2{top:224px}.r3{top:419px}.r4{top:613px}.r5{top:808px}.r6{top:1002px}
.art{position:absolute;left:0;top:0;width:312px;height:176px}
.abs{position:absolute}
.logo{position:absolute;font-weight:700;color:var(--navy);font-size:5.5px;letter-spacing:.2px;white-space:nowrap}
.logo.big{font-size:10px;color:#fff}
.logo.mid{font-size:13px;color:#fff}
.logo.small{font-size:4.6px}
.kicker{font-weight:300;color:var(--teal);font-size:11px;line-height:1.1;text-transform:uppercase}
.title{font-weight:700;color:var(--navy);font-size:11px;line-height:1.15;text-transform:uppercase}
.title.lc,.kicker.lc{text-transform:none}
.sub{font-weight:300;color:var(--muted);font-size:6.6px;line-height:1.5}
.body{font-size:3.3px;line-height:1.5;color:#6a7076;text-align:justify}
.body b{color:#333}
.white{color:#fff!important}
.right{text-align:right}
.foot{position:absolute;bottom:5px;font-size:3px;color:#888}
.foot.l{left:23px}.foot.r{right:20px}
.item-h{font-size:5.4px;color:var(--blue)}
.item-b{font-size:3px;line-height:1.45;color:#777}
.ring-label{font-size:5px;fill:var(--ink)}
.label{position:absolute;font-size:5.6px;color:#fff;text-transform:uppercase}
.card{position:absolute;background:#fff;width:48px;height:42px;text-align:center;padding-top:4px;box-shadow:0 1px 3px rgba(0,0,0,.15)}
.card h4{font-size:4.6px;font-weight:400;color:#222;margin-top:2px}
.card p{font-size:2.8px;color:#999;line-height:1.5;padding:1px 3px}
.badge{position:absolute;width:16px;height:16px;border-radius:50%;background:var(--teal);border:2px solid #fff;color:#fff;font-size:6px;font-weight:700;display:flex;align-items:center;justify-content:center}
.month{font-size:4.8px;color:#333}
</style>
</head>
<body>
<svg class="defs" aria-hidden="true">
  <defs>
    <linearGradient id="warm" x1="0" y1="0" x2="1" y2="1"><stop offset="0" stop-color="#6d6a63"/><stop offset=".5" stop-color="#4a4a48"/><stop offset="1" stop-color="#2f3136"/></linearGradient>
    <linearGradient id="cafe" x1="0" y1="0" x2="1" y2="1"><stop offset="0" stop-color="#3a3430"/><stop offset=".6" stop-color="#7a6450"/><stop offset="1" stop-color="#c8b8a2"/></linearGradient>
    <linearGradient id="office" x1="0" y1="0" x2="1" y2="1"><stop offset="0" stop-color="#d8d8d4"/><stop offset=".5" stop-color="#8e8a84"/><stop offset="1" stop-color="#a8866a"/></linearGradient>
    <linearGradient id="night" x1="0" y1="0" x2="1" y2="1"><stop offset="0" stop-color="#5a4a40"/><stop offset=".5" stop-color="#2a2428"/><stop offset="1" stop-color="#3a3a6a"/></linearGradient>
    <linearGradient id="brand" x1="0" y1="0" x2="1" y2="1"><stop offset="0" stop-color="#1663b0"/><stop offset="1" stop-color="#1f9aa0"/></linearGradient>
    <linearGradient id="brandV" x1="0" y1="1" x2="1" y2="0"><stop offset="0" stop-color="#0f4f9c"/><stop offset="1" stop-color="#2aa2a8"/></linearGradient>
    <linearGradient id="tealwash" x1="0" y1="0" x2="1" y2="1"><stop offset="0" stop-color="#3f8a86" stop-opacity=".9"/><stop offset="1" stop-color="#1d6a5e" stop-opacity=".95"/></linearGradient>
    <linearGradient id="bluewash" x1="0" y1="0" x2="1" y2="0"><stop offset="0" stop-color="#0f4f9c" stop-opacity=".95"/><stop offset="1" stop-color="#1f9aa0" stop-opacity=".85"/></linearGradient>
  </defs>
</svg>

<!-- Row 1 -->
<section class="slide c1 r1">
  <svg class="art" viewBox="0 0 312 176" role="img" aria-label="Photo of colleagues laughing around a laptop, teal tint"><rect width="312" height="176" fill="url(#warm)"/><rect width="312" height="176" fill="url(#tealwash)"/></svg>
  <div class="logo big" style="left:58px;top:136px">CREWVLT</div>
  <div class="abs white" style="left:118px;top:108px;font-size:11px;line-height:1.15;text-transform:uppercase"><span style="font-weight:300">Presentation title</span><br><b>Slide goes here</b></div>
  <div class="abs white" style="left:118px;top:136px;font-size:6.6px;font-weight:300;line-height:1.6">You could place here a extended<br>subtitle for the slide</div>
</section>

<section class="slide c2 r1">
  <svg class="art" viewBox="0 0 312 176" role="img" aria-label="Photo of colleagues laughing around a laptop"><rect width="312" height="176" fill="url(#warm)"/></svg>
  <svg class="art" viewBox="0 0 312 176" aria-hidden="true"><polygon points="0,0 235,0 120,176 0,176" fill="url(#bluewash)"/><polygon points="180,0 235,0 160,115" fill="#2aa2a8" opacity=".6"/></svg>
  <div class="logo mid" style="left:32px;top:44px">CREWVLT</div>
  <div class="abs white" style="left:32px;top:65px;font-size:11px;line-height:1.2;text-transform:uppercase"><span style="font-weight:300">Your title</span><br><b>Slide here</b></div>
  <p class="body white abs" style="left:32px;top:95px;width:92px;color:#e6eef5"><b style="color:#fff">Lorem Ipsum</b> is simply dummy text of the printing and typesetting industry. Lorem Ipsum has been the industry's standard dummy text ever since the 1500s, when an unknown printer took a galley of type and scrambled it to make a type specimen book. It has survived not only five centuries.</p>
</section>

<section class="slide c3 r1">
  <svg class="art" viewBox="0 0 312 176" role="img" aria-label="Photo of a team gathered around laptops in an office"><polygon points="0,0 205,0 95,176 0,176" fill="url(#office)"/><polygon points="175,70 205,70 140,176 100,176" fill="url(#brandV)" opacity=".9"/></svg>
  <div class="logo" style="right:18px;top:20px">CREWVLT</div>
  <div class="abs right" style="right:24px;top:38px"><div class="kicker">Place here</div><div class="title">Your title slide</div></div>
  <div class="sub abs right" style="right:24px;top:66px">You could place here a<br>extended subtitle for the slide</div>
  <p class="body abs" style="right:24px;top:99px;width:102px;text-align:center"><b>Lorem Ipsum</b> is simply dummy text of the printing and typesetting industry. Lorem Ipsum has been the industry's standard dummy text ever since the 1500s, when an unknown printer took a galley of type and scrambled it to make a type specimen book. It has survived not only five centuries.</p>
  <div class="foot r">www.crewvlt.com/ &nbsp; Page:3</div>
</section>

<!-- Row 2 -->
<section class="slide c1 r2">
  <svg class="art" viewBox="0 0 312 176" role="img" aria-label="Photo of colleagues looking at a laptop screen"><polygon points="240,0 312,0 312,176 120,176" fill="url(#night)"/><polygon points="225,0 250,0 150,150 138,135" fill="url(#brandV)"/></svg>
  <div class="logo" style="left:23px;top:21px">CREWVLT</div>
  <div class="abs" style="left:20px;top:40px"><div class="kicker">Place here</div><div class="title">Your title slide</div></div>
  <div class="sub abs" style="left:20px;top:72px">You could place subtitle slide</div>
  <p class="body abs" style="left:20px;top:86px;width:105px">Lorem ipsum is simply dummy text of the printing and typesetting industry. Lorem ipsum has been the industry's standard dummy text ever since the 1500s, when an unknown printer took a galley of type and scrambled it to make a type specimen book. It has survived not only five centuries, but also the leap into electronic typesetting, remaining essentially unchanged. It was popularised in the 1960s with the release of sheets.</p>
  <div class="foot l">Integrity &nbsp;Family &nbsp;Respect &nbsp;Passion</div>
  <div class="foot r">www.crewvlt.com/ &nbsp; Page:7</div>
</section>

<section class="slide c2 r2">
  <svg class="art" viewBox="0 0 312 176" role="img" aria-label="Photo of young professionals sitting on outdoor steps with laptops"><polygon points="0,0 200,0 110,176 0,176" fill="url(#cafe)"/><polygon points="312,120 312,176 270,176" fill="url(#brandV)"/></svg>
  <svg class="art" viewBox="0 0 312 176" aria-hidden="true"><polygon points="146,80 174,80 168,92 140,92" fill="var(--gold)"/><polygon points="130,108 158,108 152,120 124,120" fill="var(--red)"/><polygon points="114,136 142,136 136,148 108,148" fill="var(--green)"/></svg>
  <div class="logo" style="right:18px;top:20px">CREWVLT</div>
  <div class="abs right" style="right:22px;top:37px"><div class="kicker">Place here</div><div class="title">Your title slide</div></div>
  <div class="abs" style="left:190px;top:78px;width:102px"><div class="item-h">Lorem Ipsum Dolor</div><div class="item-b">Lorem ipsum is simply dummy text of the printing and typesetting industry. Lorem ipsum has been the industry's standard dummy text ever since the 1500s.</div></div>
  <div class="abs" style="left:174px;top:106px;width:102px"><div class="item-h">Lorem Ipsum Dolor</div><div class="item-b">Lorem ipsum is simply dummy text of the printing and typesetting industry. Lorem ipsum has been the industry's standard dummy text ever since the 1500s.</div></div>
  <div class="abs" style="left:158px;top:134px;width:102px"><div class="item-h">Lorem Ipsum Dolor</div><div class="item-b">Lorem ipsum is simply dummy text of the printing and typesetting industry. Lorem ipsum has been the industry's standard dummy text ever since the 1500s.</div></div>
  <div class="foot r">www.crewvlt.com/ &nbsp; Page:5</div>
</section>

<section class="slide c3 r2">
  <svg class="art" viewBox="0 0 312 176" role="img" aria-label="Photo of colleagues looking at a laptop screen"><polygon points="210,0 312,0 312,176 110,176" fill="url(#night)"/><polygon points="195,0 222,0 120,160 108,145" fill="url(#brandV)"/></svg>
  <svg class="art" viewBox="0 0 312 176" aria-hidden="true"><polygon points="26,102 42,102 38,109 22,109" fill="var(--gold)"/><polygon points="26,130 42,130 38,137 22,137" fill="var(--red)"/></svg>
  <div class="logo" style="left:23px;top:21px">CREWVLT</div>
  <div class="abs" style="left:23px;top:38px"><div class="kicker">Place here</div><div class="title">Your title slide</div></div>
  <div class="sub abs" style="left:23px;top:70px">You could place here a<br>extended subtitle for the slide</div>
  <div class="abs" style="left:48px;top:100px;width:70px"><div class="item-h">Lorem Ipsum Dolor</div><div class="item-b">Lorem ipsum dolor sit amet, consectetur adipiscing elit. Morbi hendrerit elit turpis.</div></div>
  <div class="abs" style="left:48px;top:128px;width:70px"><div class="item-h">Lorem Ipsum Dolor</div><div class="item-b">Lorem ipsum dolor sit amet, consectetur adipiscing elit. Morbi hendrerit elit turpis.</div></div>
  <div class="foot l">Integrity &nbsp;Family &nbsp;Respect &nbsp;Passion</div>
</section>

<!-- Row 3 -->
<section class="slide c1 r3">
  <svg class="art" viewBox="0 0 312 176" role="img" aria-label="Photo of smiling women at a cafe table"><polygon points="215,0 312,0 312,176 125,176" fill="url(#cafe)"/><polygon points="205,0 222,0 155,100 140,95" fill="url(#brandV)"/></svg>
  <div class="logo" style="left:23px;top:21px">CREWVLT</div>
  <div class="abs" style="left:23px;top:38px"><div class="kicker">Place here</div><div class="title">Your title slide</div></div>
  <div class="sub abs" style="left:23px;top:70px">You could place here a<br>extended subtitle for the slide</div>
  <p class="body abs" style="left:25px;top:99px;width:107px;text-align:left"><b>Lorem Ipsum</b> is simply dummy text of the printing and typesetting industry. Lorem Ipsum has been the industry's standard dummy text ever since the 1500s, when an unknown printer took a galley of type and scrambled it to make a type specimen book. It has survived not only five centuries.</p>
  <div class="foot l">Integrity &nbsp;Family &nbsp;Respect &nbsp;Passion</div>
</section>

<section class="slide c2 r3">
  <svg class="art" viewBox="0 0 312 176" role="img" aria-label="Photo of colleagues laughing around a laptop in a library"><polygon points="130,62 312,62 312,152 72,152" fill="url(#warm)"/></svg>
  <svg class="art" viewBox="0 0 312 176" aria-hidden="true"><polygon points="27,0 117,0 117,60 27,152" fill="url(#brandV)"/></svg>
  <div class="abs white" style="left:36px;top:36px;font-size:11px;line-height:1.2;text-transform:uppercase"><span style="font-weight:300">Place here</span><br><b>Your title<br>slide</b></div>
  <div class="card" style="left:134px;top:36px"><svg width="9" height="9" viewBox="0 0 10 10" aria-hidden="true"><circle cx="5" cy="5" r="3" fill="none" stroke="#222" stroke-width="2" stroke-dasharray="1.5 1"/><circle cx="5" cy="5" r="1" fill="#222"/></svg><h4>Your Text</h4><p>A wonderful serenity has taken possession of my entire soul, like these sweet mornings</p></div>
  <div class="card" style="left:216px;top:36px"><svg width="9" height="9" viewBox="0 0 10 10" aria-hidden="true"><path d="M2 1h6M2 9h6M3 1l4 4-4 4M7 1L3 5l4 4" fill="none" stroke="#222" stroke-width="1"/></svg><h4>Your Text</h4><p>A wonderful serenity has taken possession of my entire soul, like these sweet</p></div>
  <div class="logo" style="right:18px;top:13px">CREWVLT</div>
  <div class="foot l">Integrity &nbsp;Family &nbsp;Respect &nbsp;Passion</div>
  <div class="foot r">www.crewvlt.com/ &nbsp; Page:11</div>
</section>

<section class="slide c3 r3">
  <svg class="art" viewBox="0 0 312 176" role="img" aria-label="Two photo panels of colleagues laughing at a laptop"><polygon points="160,12 222,12 168,108 110,108" fill="url(#warm)"/><polygon points="232,45 312,45 312,60 250,150 200,150" fill="url(#warm)"/></svg>
  <div class="logo" style="right:18px;top:13px">CREWVLT</div>
  <div class="abs" style="left:23px;top:30px"><div class="kicker">Place here</div><div class="title">Your title slide</div></div>
  <div class="sub abs" style="left:23px;top:62px;font-size:5.6px">You could place subtitle slide</div>
  <p class="body abs" style="left:23px;top:75px;width:86px">Lorem ipsum is simply dummy text of the printing and typesetting industry. Lorem ipsum has been the industry's standard dummy text ever since the 1500s, when an unknown printer took a galley of type and scrambled it to make a type specimen book. It has survived not only five centuries, but also the leap into electronic typesetting, remaining essentially unchanged. It was popularised in the 1960s with the release of sheets.</p>
  <p class="body abs" style="left:23px;top:131px;width:165px">Contrary to popular belief, Lorem Ipsum is not simply random text. It has roots in a piece of classical Latin literature from 45 BC, making it over 2000 years old. A Latin professor looked up one of the more obscure Latin words, consectetur, from a Lorem Ipsum passage, and going through the cites of the word in classical literature, discovered the undoubtable source.</p>
  <div class="foot l">Integrity &nbsp;Family &nbsp;Respect &nbsp;Passion</div>
  <div class="foot r">www.crewvlt.com/ &nbsp; Page:8</div>
</section>

<!-- Row 4 -->
<section class="slide c1 r4">
  <svg class="art" viewBox="0 0 312 176" role="img" aria-label="Photo of smiling women at a cafe table"><polygon points="0,0 40,0 0,75" fill="url(#brandV)"/><polygon points="103,27 179,27 104,147 30,147" fill="url(#cafe)"/></svg>
  <div class="logo" style="right:18px;top:13px">CREWVLT</div>
  <div class="abs right" style="right:24px;top:37px"><div class="kicker lc">Place Here</div><div class="title lc">your title slide</div></div>
  <div class="sub abs right" style="right:24px;top:68px">You could place here a<br>extended subtitle for the slide</div>
  <svg class="abs" style="left:145px;top:97px" width="150" height="26" viewBox="0 0 150 26" aria-hidden="true">
    <g fill="none" stroke-width="1.4">
      <circle cx="12" cy="13" r="11" stroke="#e3e3e3"/><circle cx="12" cy="13" r="11" stroke="var(--blue)" stroke-dasharray="58.7 69" transform="rotate(-90 12 13)"/>
      <circle cx="51" cy="13" r="11" stroke="#e3e3e3"/><circle cx="51" cy="13" r="11" stroke="var(--green)" stroke-dasharray="44.9 69" transform="rotate(-90 51 13)"/>
      <circle cx="90" cy="13" r="11" stroke="#e3e3e3"/><circle cx="90" cy="13" r="11" stroke="var(--gold)" stroke-dasharray="65.6 69" transform="rotate(-90 90 13)"/>
      <circle cx="129" cy="13" r="11" stroke="var(--red)"/>
    </g>
    <text class="ring-label" x="12" y="15" text-anchor="middle">85%</text><text class="ring-label" x="51" y="15" text-anchor="middle">65%</text><text class="ring-label" x="90" y="15" text-anchor="middle">95%</text><text class="ring-label" x="129" y="15" text-anchor="middle">100%</text>
  </svg>
  <p class="item-b abs" style="left:142px;top:131px;width:30px;font-size:2.8px">Lorem ipsum is simply dummy text of the printing and typesetting</p>
  <p class="item-b abs" style="left:181px;top:131px;width:30px;font-size:2.8px">Lorem ipsum is simply dummy text of the printing and typesetting</p>
  <p class="item-b abs" style="left:220px;top:131px;width:30px;font-size:2.8px">Lorem ipsum is simply dummy text of the printing and typesetting</p>
  <p class="item-b abs" style="left:259px;top:131px;width:30px;font-size:2.8px">Lorem ipsum is simply dummy text of the printing and typesetting</p>
  <div class="foot l">Integrity &nbsp;Family &nbsp;Respect &nbsp;Passion</div>
  <div class="foot r">www.crewvlt.com/ &nbsp; Page:10</div>
</section>

<section class="slide c2 r4">
  <svg class="art" viewBox="0 0 312 176" role="img" aria-label="Photo of a team working on laptops at a long table"><rect width="312" height="176" fill="url(#night)"/></svg>
  <svg class="art" viewBox="0 0 312 176" aria-hidden="true"><polygon points="312,0 312,176 110,176 230,0" fill="#1f8a9a" opacity=".85"/><polygon points="230,0 312,0 312,40 260,0" fill="#1663b0" opacity=".7"/></svg>
  <div class="logo mid" style="right:35px;top:50px">CREWVLT</div>
  <div class="abs white right" style="right:35px;top:70px;font-size:11px;line-height:1.2;text-transform:uppercase;font-weight:300">Your title<br>slide here</div>
  <p class="body white abs" style="left:183px;top:100px;width:95px;color:#e6f0f2"><b style="color:#fff">Lorem Ipsum</b> is simply dummy text of the printing and typesetting industry. Lorem Ipsum has been the industry's standard dummy text ever since the 1500s, when an unknown printer took a galley of type and scrambled it to make a type specimen book. It has survived not only five centuries.</p>
</section>

<section class="slide c3 r4">
  <svg class="art" viewBox="0 0 312 176" role="img" aria-label="Photo of colleagues laughing at a laptop"><polygon points="150,27 230,27 155,148 75,148" fill="url(#warm)"/></svg>
  <div class="logo" style="right:18px;top:13px">CREWVLT</div>
  <div class="abs" style="left:22px;top:37px"><div class="kicker lc">Place here</div><div class="title lc">your title slide</div></div>
  <p class="body abs" style="left:24px;top:76px;width:68px">Lorem ipsum is simply dummy text of the printing and typesetting industry. Lorem ipsum has been the industry's standard dummy text ever since the 1500s, when an unknown printer took a galley of type and scrambled it to make a type specimen book. It has survived not only five centuries, but also the leap into electronic typesetting, remaining essentially unchanged. It was popularised with desktop publishing software.</p>
  <div class="sub abs right" style="right:22px;top:40px;font-size:8px">Place here a<br>subtitle slide</div>
  <p class="body abs right" style="right:20px;top:68px;width:68px;text-align:right">Contrary to popular belief, Lorem Ipsum is not simply random text. It has roots in a piece of classical Latin literature from 45 BC, making it over 2000 years old. A Latin professor looked up one of the words.</p>
  <p class="body abs right" style="right:20px;top:105px;width:95px;text-align:right">The more obscure Latin words, consectetur, from a Lorem Ipsum passage, and going through the cites of the word in classical literature, discovered the undoubtable source. Lorem Ipsum comes from sections 1.10.32 and 1.10.33 of an ancient text, written in 45 BC. This book.</p>
  <div class="foot l">Integrity &nbsp;Family &nbsp;Respect &nbsp;Passion</div>
  <div class="foot r">www.crewvlt.com/ &nbsp; Page:12</div>
</section>

<!-- Row 5 -->
<section class="slide c1 r5">
  <svg class="art" viewBox="0 0 312 176" aria-hidden="true"><rect x="0" y="36" width="312" height="84" fill="url(#brand)"/></svg>
  <svg class="art" viewBox="0 0 312 176" role="img" aria-label="Three photos: restaurant interior, real estate aerial view, development team"><polygon points="52,38 140,38 100,120 15,120" fill="url(#cafe)"/><polygon points="135,38 220,38 178,120 94,120" fill="#6e8a5a"/><polygon points="215,38 295,38 255,120 172,120" fill="url(#office)"/></svg>
  <div class="abs" style="left:23px;top:12px;font-size:12px;color:var(--blue)"><span style="font-weight:300">WHAT</span> <b>WE DO</b></div>
  <div class="logo" style="right:18px;top:16px">CREWVLT</div>
  <div class="label" style="left:36px;top:112px">Restaurants</div>
  <div class="label" style="left:116px;top:112px">Real Estate</div>
  <div class="label" style="left:191px;top:112px">Development</div>
  <p class="body abs" style="left:25px;top:127px;width:266px">Lorem ipsum is simply dummy text of the printing and typesetting industry. Lorem ipsum has been the industry's standard dummy text ever since the 1500s, when an unknown printer took a galley of type and scrambled it to make a type specimen book. It has survived not only five centuries, but also the leap into electronic typesetting, remaining essentially unchanged. It was popularised in the 1960s with the release of sheets containing Lorem Ipsum passages, and more recently with desktop publishing software including versions of Lorem Ipsum. Contrary to popular belief, Lorem Ipsum is not simply random text. It has roots in a piece of classical Latin literature from 45 BC, making it over 2000 years old.</p>
  <div class="foot l">Integrity &nbsp;Family &nbsp;Respect &nbsp;Passion</div>
  <div class="foot r">www.crewvlt.com/ &nbsp; Page:13</div>
</section>

<section class="slide c2 r5">
  <svg class="art" viewBox="0 0 312 176" aria-hidden="true"><rect x="0" y="60" width="312" height="56" fill="url(#brand)"/></svg>
  <svg class="art" viewBox="0 0 312 176" role="img" aria-label="Two group photos of young colleagues"><polygon points="148,38 297,38 297,98 186,98" fill="url(#office)"/><polygon points="15,64 145,64 165,122 15,122" fill="url(#cafe)"/><polygon points="148,38 297,38 297,98 186,98" fill="#1663b0" opacity=".25"/></svg>
  <div class="logo" style="right:18px;top:13px">CREWVLT</div>
  <div class="abs" style="left:23px;top:18px;font-size:5.6px;line-height:1.1;color:var(--blue);text-transform:uppercase">You could place here a<br><b>subtitle for the slide</b></div>
  <p class="body abs" style="left:23px;top:33px;width:105px;text-align:left">Lorem ipsum is simply dummy text of the printing and typesetting industry. Lorem ipsum has been the industry's standard dummy.</p>
  <div class="abs white right" style="right:18px;top:83px;font-size:5.4px;line-height:1.1;text-transform:uppercase">You could place<br>here a subtitle for<br>the slide</div>
  <div class="abs white" style="left:26px;top:112px;font-size:5.4px;line-height:1.1;text-transform:uppercase">You could place here a<br>subtitle for the slide</div>
  <div class="abs right" style="right:22px;top:127px;font-size:5.6px;line-height:1.1;color:var(--blue);text-transform:uppercase">You could place here a<br><b>subtitle for the slide here</b></div>
  <p class="body abs right" style="right:22px;top:142px;width:105px;text-align:right">Lorem ipsum is simply dummy text of the printing and typesetting industry. Lorem ipsum has been the industry's standard dummy.</p>
  <div class="foot l">Integrity &nbsp;Family &nbsp;Respect &nbsp;Passion</div>
  <div class="foot r">www.crewvlt.com/ &nbsp; Page:15</div>
</section>

<section class="slide c3 r5">
  <svg class="art" viewBox="0 0 312 176" role="img" aria-label="Photo of a team gathered around laptops in an office"><polygon points="170,0 295,0 230,110 150,110" fill="url(#office)"/></svg>
  <svg class="art" viewBox="0 0 312 176" aria-hidden="true"><polygon points="27,136 43,136 39,142 23,142" fill="var(--gold)"/><polygon points="122,136 138,136 134,142 118,142" fill="var(--red)"/><polygon points="217,136 233,136 229,142 213,142" fill="var(--green)"/></svg>
  <div class="logo small" style="left:19px;top:18px">CREWVLT</div>
  <div class="abs" style="left:47px;top:14px"><div class="kicker">Project</div><div class="title">Timeline<br>Start</div></div>
  <p class="body abs" style="left:21px;top:63px;width:125px">Lorem ipsum is simply dummy text of the printing and typesetting industry. Lorem ipsum has been the industry's standard dummy text ever since the 1500s, when an unknown printer took a galley of type and scrambled it to make a type specimen book. It has survived not only five centuries, but also the leap into electronic typesetting, remaining essentially unchanged. It was popularised in the 1960s with the release of sheets containing passages, and more recently with desktop publishing software.</p>
  <p class="body abs" style="left:21px;top:113px;width:270px">Contrary to popular belief, Lorem Ipsum is not simply random text. It has roots in a piece of classical Latin literature from 45 BC, making it over 2000 years old. A Latin professor looked up one of the more obscure Latin words, consectetur, from a Lorem Ipsum passage, and going through the cites of the word in classical literature, discovered the undoubtable source.</p>
  <div class="abs" style="left:48px;top:134px;width:55px"><div class="item-h">Lorem Ipsum Dolor</div><div class="item-b">Lorem ipsum dolor sit amet, consectetur adipiscing elit. Morbi hendrerit elit turpis.</div></div>
  <div class="abs" style="left:143px;top:134px;width:55px"><div class="item-h">Lorem Ipsum Dolor</div><div class="item-b">Lorem ipsum dolor sit amet, consectetur adipiscing elit. Morbi hendrerit elit turpis.</div></div>
  <div class="abs" style="left:238px;top:134px;width:55px"><div class="item-h">Lorem Ipsum Dolor</div><div class="item-b">Lorem ipsum dolor sit amet, consectetur adipiscing elit. Morbi hendrerit elit turpis.</div></div>
  <div class="foot l">Integrity &nbsp;Family &nbsp;Respect &nbsp;Passion</div>
  <div class="foot r">www.crewvlt.com/ &nbsp; Page:16</div>
</section>

<!-- Row 6 -->
<section class="slide c1 r6">
  <svg class="art" viewBox="0 0 312 176" role="img" aria-label="Two photos of colleagues working together at laptops"><polygon points="70,0 105,0 47,104 12,104" fill="url(#cafe)"/><polygon points="200,0 235,0 177,104 142,104" fill="url(#night)"/></svg>
  <div class="badge" style="left:99px;top:17px">18</div>
  <div class="badge" style="left:229px;top:17px">2</div>
  <div class="logo" style="right:18px;top:13px">CREWVLT</div>
  <div class="abs" style="left:112px;top:44px;width:48px"><div class="month">February</div><div class="item-b" style="color:var(--blue)">Lorem ipsum is simply dummy text of the printing and typesetting industry. Lorem ipsum has been the industry's standard dummy text ever since the 1500s, when an unknown printer took a galley of type and scrambled.</div></div>
  <div class="abs" style="left:243px;top:44px;width:48px"><div class="month">April</div><div class="item-b" style="color:var(--blue)">Lorem ipsum is simply dummy text of the printing and typesetting industry. Lorem ipsum has been the industry's standard dummy text ever since the 1500s, when an unknown printer took a galley of type and scrambled.</div></div>
  <div class="abs" style="left:22px;top:120px"><div class="kicker">Project</div><div class="title">Timeline</div></div>
  <p class="body abs" style="left:91px;top:120px;width:200px">Lorem ipsum is simply dummy text of the printing and typesetting industry. Lorem ipsum has been the industry's standard dummy text ever since the 1500s, when an unknown printer took a galley of type and scrambled it to make a type specimen book. It has survived not only five centuries, but also the leap into electronic typesetting, remaining essentially unchanged. It was popularised in the 1960s with desktop publishing software. Contrary to popular belief, it has roots in classical Latin literature from 45 BC.</p>
  <div class="foot l">Integrity &nbsp;Family &nbsp;Respect &nbsp;Passion</div>
  <div class="foot r">www.crewvlt.com/ &nbsp; Page:17</div>
</section>

<section class="slide c2 r6">
  <svg class="art" viewBox="0 0 312 176" role="img" aria-label="Two photos of colleagues working together at laptops"><polygon points="70,0 105,0 47,104 12,104" fill="url(#cafe)"/><polygon points="200,0 235,0 177,104 142,104" fill="url(#night)"/></svg>
  <div class="badge" style="left:99px;top:17px">24</div>
  <div class="badge" style="left:229px;top:17px">16</div>
  <div class="logo" style="right:18px;top:13px">CREWVLT</div>
  <div class="abs" style="left:112px;top:44px;width:48px"><div class="month">June</div><div class="item-b" style="color:var(--blue)">Lorem ipsum is simply dummy text of the printing and typesetting industry. Lorem ipsum has been the industry's standard dummy text ever since the 1500s, when an unknown printer took a galley of type and scrambled.</div></div>
  <div class="abs" style="left:243px;top:44px;width:48px"><div class="month">July</div><div class="item-b" style="color:var(--blue)">Lorem ipsum is simply dummy text of the printing and typesetting industry. Lorem ipsum has been the industry's standard dummy text ever since the 1500s, when an unknown printer took a galley of type and scrambled.</div></div>
  <div class="abs" style="left:22px;top:120px"><div class="kicker lc">Project</div><div class="title lc">Timeline</div></div>
  <p class="body abs" style="left:85px;top:120px;width:206px">Lorem ipsum is simply dummy text of the printing and typesetting industry. Lorem ipsum has been the industry's standard dummy text ever since the 1500s, when an unknown printer took a galley of type and scrambled it to make a type specimen book. It has survived not only five centuries, but also the leap into electronic typesetting, remaining essentially unchanged. It was popularised with desktop publishing software. Contrary to popular belief, it has roots in classical Latin literature from 45 BC, making it over 2000 years old.</p>
  <div class="foot l">Integrity &nbsp;Family &nbsp;Respect &nbsp;Passion</div>
  <div class="foot r">www.crewvlt.com/ &nbsp; Page:18</div>
</section>

<section class="slide c3 r6">
  <svg class="art" viewBox="0 0 312 176" role="img" aria-label="Photo of smiling women at a cafe table"><polygon points="45,0 172,0 110,105 0,105 0,80" fill="url(#cafe)"/></svg>
  <div class="logo" style="right:18px;top:13px">CREWVLT</div>
  <div class="abs" style="left:176px;top:13px"><div class="kicker">Project</div><div class="title">Timeline<br>Finish</div></div>
  <p class="body abs" style="left:176px;top:52px;width:118px">Lorem ipsum is simply dummy text of the printing and typesetting industry. Lorem ipsum has been the industry's standard dummy text ever since the 1500s, when an unknown printer took a galley of type and scrambled it to make a type specimen book. It has survived not only five centuries, but also the leap into electronic typesetting, remaining essentially unchanged. It was popularised in the 1960s with the release of sheets containing passages, and more recently with desktop publishing software.</p>
  <p class="body abs" style="left:148px;top:112px;width:146px">Lorem ipsum is simply dummy text of the printing and typesetting industry. Lorem ipsum has been the industry's standard dummy text ever since the 1500s. Contrary to popular belief, Lorem Ipsum is not simply random text. It has roots in a piece of classical Latin literature from 45 BC, making it over 2000 years old. A Latin professor looked up one of the more obscure Latin words, consectetur, from a passage, and going through the cites of the word in classical literature, discovered the undoubtable source.</p>
  <svg class="abs" style="left:19px;top:110px" width="115" height="26" viewBox="0 0 115 26" aria-hidden="true">
    <g fill="none" stroke-width="1.4">
      <circle cx="13" cy="13" r="11" stroke="#e3e3e3"/><circle cx="13" cy="13" r="11" stroke="var(--gold)" stroke-dasharray="65.6 69" transform="rotate(-90 13 13)"/>
      <circle cx="56" cy="13" r="11" stroke="var(--red)"/>
      <circle cx="99" cy="13" r="11" stroke="#e3e3e3"/><circle cx="99" cy="13" r="11" stroke="var(--green)" stroke-dasharray="65.6 69" transform="rotate(-90 99 13)"/>
    </g>
    <text class="ring-label" x="13" y="15" text-anchor="middle">95%</text><text class="ring-label" x="56" y="15" text-anchor="middle">100%</text><text class="ring-label" x="99" y="15" text-anchor="middle">95%</text>
  </svg>
  <p class="item-b abs" style="left:19px;top:140px;width:28px;font-size:2.8px">Lorem ipsum is simply dummy text of the printing and typesetting</p>
  <p class="item-b abs" style="left:62px;top:140px;width:28px;font-size:2.8px">Lorem ipsum is simply dummy text of the printing and typesetting</p>
  <p class="item-b abs" style="left:105px;top:140px;width:28px;font-size:2.8px">Lorem ipsum is simply dummy text of the printing and typesetting</p>
  <div class="foot l">Integrity &nbsp;Family &nbsp;Respect &nbsp;Passion</div>
  <div class="foot r">www.crewvlt.com/ &nbsp; Page:19</div>
</section>
</body>
</html>
```